Web design for business website

I need a web design for a business website for one of our clients who is specialized in alarm management software. I would like you to design 3 web pages, one for each of the 3 pages. You need to process the corporate identity of our client to the web design. This means the colors of the logo (red and black) should definitely show up on all of the 3 pages. Find the logo file for the logo of our customer. To increase readability I suggest you use a white/light background. All suggestions are welcome.

Please kindly download atttached Webdesign.zip and read the project brief first. The project brief refers to all other files of the zip file. Your design must have exactly the same structure as the wireframes.
Updates

Target Market(s)

B2B, Alarm management

Industry/Entity Type

Business

Number of Pages Required

3 page

Requirements
Must have
• The web design must have exactly the same structure as the wireframes and needs to contain the colors of the company logo.

```html
<!DOCTYPE html>
<html lang="en">
<head>
<meta charset="utf-8">
<title>Kalveron – Real-time reasoning solutions</title>
<link href="https://fonts.googleapis.com/css2?family=Raleway:wght@300;400;500;800&family=Open+Sans:wght@400;600&display=swap" rel="stylesheet">
<style>
:root{
  --red:#c9381a;
  --red-dark:#6d1a10;
  --red-active:#a52d14;
  --black:#0b0b0b;
  --ink:#1c1b2b;
  --text:#333;
  --grey-bar:#e8e8e8;
  --footer:#1e1e1e;
  --footer-text:#d6d6d6;
  --hero-top:#9a8a6c;
  --hero-bottom:#6f6550;
}
*{margin:0;padding:0;box-sizing:border-box}
html,body{width:1068px;height:1200px;overflow:hidden;background:#fff}
body{position:relative;font-family:"Open Sans",sans-serif;color:var(--text)}
.abs{position:absolute}
a{color:inherit;text-decoration:none}

.topbar{left:0;top:0;width:1068px;height:32px;background:var(--grey-bar)}
.topbar .phone{left:129px;top:9px;font-size:11px;color:#333}
.topbar .lang{left:732px;top:10px;font-size:11px;color:#444}
.topbar .lang:after{content:"";display:inline-block;margin-left:5px;border:4px solid transparent;border-top:5px solid #555;vertical-align:-2px}
.search{left:788px;top:5px;width:160px;height:21px;background:#fff;border:1px solid #ccc;font-size:8px;color:#666;padding:5px 7px}
.search svg{position:absolute;right:6px;top:4px}

.brand{left:119px;top:52px}
.brand .name{position:absolute;left:65px;top:1px;font-family:"Raleway",sans-serif;font-weight:800;font-size:37px;letter-spacing:2px;color:var(--ink);line-height:1;white-space:nowrap}
.brand .tag{position:absolute;left:66px;top:39px;font-size:11px;color:#222;white-space:nowrap}

.btn{top:50px;height:54px;width:71px;color:#fff;font-size:11px;text-align:center;padding-top:8px}
.btn svg{display:block;margin:0 auto 3px}
.btn-account{left:726px;background:#f0f0f0;border:1px solid #ccc;color:#333}
.btn-login{left:802px;width:70px;background:var(--red)}
.btn-signup{left:877px;background:var(--black)}

.nav{left:0;top:119px;width:1068px;height:38px;background:linear-gradient(#d4421d,#c1331a)}
.nav a{position:absolute;top:12px;font-family:"Raleway",sans-serif;font-size:13px;color:#fff;font-weight:500}
.nav .active{left:198px;top:0;width:97px;height:38px;background:var(--red-active)}

.hero{left:0;top:157px;width:1068px;height:356px;background:linear-gradient(180deg,var(--hero-top),var(--hero-bottom))}
.hero-arrow{top:305px;width:35px;height:41px;background:#111;display:flex;align-items:center;justify-content:center}

.dropdown{left:198px;top:157px;width:380px;height:145px;background:var(--red-dark)}
.dropdown .thumb{position:absolute;left:24px;top:19px;width:189px;height:85px;border:2px solid #fff;background:#4a5670}
.dropdown .caption{position:absolute;left:24px;top:113px;font-family:"Raleway",sans-serif;font-size:11px;color:#fff}
.dropdown ul{position:absolute;left:236px;top:21px;list-style:none}
.dropdown li{font-family:"Raleway",sans-serif;font-size:11.5px;color:#fff;height:22.7px;white-space:nowrap}

.about{left:0;top:555px;width:1068px;text-align:center}
.about h1{font-family:"Raleway",sans-serif;font-weight:400;font-size:28px;color:#222;letter-spacing:.5px}
.about p{width:790px;margin:9px auto 0;font-size:9.6px;line-height:15.6px;color:#333}
.about p+p{margin-top:10px}

.clients-title{left:0;top:740px;width:1068px;text-align:center;font-family:"Raleway",sans-serif;font-size:19px;color:var(--red)}
.clients-nav{left:921px;top:751px}
.clients-rule{left:123px;top:772px;width:826px;height:1px;background:#ddd}
.clients{left:123px;top:800px;width:826px;display:flex;justify-content:space-around;align-items:center}
.client{font-family:"Open Sans",sans-serif;font-weight:600;font-size:17px;color:#555;white-space:nowrap}

.strip{left:0;top:887px;width:1068px;height:53px;background:#000}
.social{top:905px;width:20px;height:20px;background:#fff;border-radius:3px}
.news-label{left:610px;top:905px;font-family:"Raleway",sans-serif;font-size:17px;color:#fff}
.news-input{left:701px;top:903px;width:162px;height:25px;background:#2b2b2b;font-size:8px;color:#888;padding:8px 9px}
.news-btn{left:863px;top:903px;width:75px;height:25px;background:var(--red);color:#fff;font-family:"Raleway",sans-serif;font-size:12px;text-align:center;padding-top:5px}

.footer{left:0;top:940px;width:1068px;height:260px;background:var(--footer)}
.col{top:966px}
.col h3{font-family:"Raleway",sans-serif;font-weight:400;font-size:16px;color:var(--red);margin-bottom:6px}
.col li{list-style:none;font-size:9.3px;color:var(--footer-text);line-height:17px;white-space:nowrap}
.col li.big{font-size:12.5px;line-height:19px}
.footer-rule{left:0;top:1139px;width:1068px;height:1px;background:#333}
.copyright{left:124px;top:1161px;font-size:9.3px;color:#888}
</style>
</head>
<body>

<div class="abs topbar">
  <div class="abs phone">T&nbsp; +31 (0)20 555 0148</div>
  <div class="abs lang">ENG</div>
  <div class="abs search">Search
    <svg width="12" height="12" viewBox="0 0 12 12"><circle cx="5" cy="5" r="3.8" fill="none" stroke="#333" stroke-width="1.5"/><line x1="7.8" y1="7.8" x2="11" y2="11" stroke="#333" stroke-width="1.6"/></svg>
  </div>
</div>

<div class="abs brand">
  <div class="name">KALVERON</div>
  <div class="tag">Real-time reasoning solutions</div>
</div>

<a class="abs btn btn-account">
  <svg width="20" height="20" viewBox="0 0 20 20"><circle cx="10" cy="6" r="5" fill="#222"/><path d="M1 20c0-6 4-8 9-8s9 2 9 8z" fill="#222"/></svg>Account</a>
<a class="abs btn btn-login">
  <svg width="18" height="20" viewBox="0 0 18 20"><path d="M4 9V6a5 5 0 0 1 10 0v3" fill="none" stroke="#fff" stroke-width="2.4"/><rect x="1" y="9" width="16" height="11" rx="1.5" fill="#fff"/></svg>Log in</a>
<a class="abs btn btn-signup">
  <svg width="22" height="20" viewBox="0 0 22 20"><rect x="1" y="4" width="15" height="15" rx="2" fill="none" stroke="#fff" stroke-width="1.8"/><path d="M8 13l1-4 9-8 3 3-9 8z" fill="none" stroke="#fff" stroke-width="1.6"/></svg>Sign up</a>

<nav class="abs nav">
  <div class="abs active"></div>
  <a style="left:145px">HOME</a>
  <a style="left:218px">INDUSTRY</a>
  <a style="left:316px">TELECOM</a>
  <a style="left:411px">POWER</a>
  <a style="left:493px">UTILITIES</a>
  <a style="left:587px">INFRA</a>
  <a style="left:659px">STORE</a>
</nav>

<div class="abs hero" role="img" aria-label="Photo: industrial plant beyond a wetland at sunset"></div>
<div class="abs hero-arrow" style="left:43px"><svg width="12" height="18" viewBox="0 0 12 18"><path d="M10 2L3 9l7 7" fill="none" stroke="#fff" stroke-width="2.6"/></svg></div>
<div class="abs hero-arrow" style="left:983px"><svg width="12" height="18" viewBox="0 0 12 18"><path d="M2 2l7 7-7 7" fill="none" stroke="#fff" stroke-width="2.6"/></svg></div>

<div class="abs dropdown">
  <div class="thumb" role="img" aria-label="Photo: refinery lit up at night"></div>
  <div class="caption">Kopteskt 5</div>
  <ul>
    <li>Alarm Management</li>
    <li>Asset Management</li>
    <li>Predictive Maintenance</li>
    <li>Logic Design</li>
  </ul>
</div>

<section class="abs about">
  <h1>ABOUT OUR COMPANY</h1>
  <p>Companies have invested to get data out of processes. New technologies have been developed to get real-time data out of the harshest places, like oil-well drill heads or the Great Barrier Riff. Data in itself means nothing without the context the data is collected in. Example: data from equipment under maintenance does not provide information to operations. Information - data which is valid and meaningful - can overwhelm any user without the proper knowledge to interpret this information.</p>
  <p>Kalveron technology enables easy application of such knowledge in a comprehensible – visual – representation and makes hypothetical reasoning with information possible providing meaningful advisories to subscribers when they need it or when it is required that they are made aware of a situation which requires their attention.</p>
</section>

<div class="abs clients-title">Our Clients</div>
<svg class="abs clients-nav" width="18" height="12" viewBox="0 0 18 12"><path d="M6 1L1 6l5 5M12 1l5 5-5 5" fill="none" stroke="#222" stroke-width="1.5"/></svg>
<div class="abs clients-rule"></div>

<div class="abs clients">
  <span class="client">Halvorn</span>
  <span class="client">Tidewell</span>
  <span class="client">Corvane</span>
  <span class="client">Mereta</span>
  <span class="client">Sunvale</span>
  <span class="client">Qadira</span>
  <span class="client">Lyncroft</span>
</div>

<div class="abs strip"></div>
<div class="abs social" style="left:124px" aria-label="Social link"></div>
<div class="abs social" style="left:150px" aria-label="Social link"></div>
<div class="abs social" style="left:177px" aria-label="Social link"></div>
<div class="abs news-label">Newsletter</div>
<div class="abs news-input">Email address</div>
<div class="abs news-btn">Subscribe</div>

<footer class="abs footer"></footer>
<div class="abs col" style="left:124px"><h3>Solutions</h3><ul><li>KAM Alarm Reporting</li><li>KAM Alarm Analysis</li><li>KAM Alarm Expert</li><li>USE</li></ul></div>
<div class="abs col" style="left:294px"><h3>Industires</h3><ul><li>Industry</li><li>Telecom</li><li>Power</li><li>Utilities</li><li>Infra</li></ul></div>
<div class="abs col" style="left:429px"><h3>About Us</h3><ul><li>Company</li><li>Overview</li><li>Leadership</li><li>Partners</li><li>Locations</li></ul></div>
<div class="abs col" style="left:556px"><h3>News</h3><ul><li>Product News</li><li>Partner News</li><li>Events</li><li>Press Releases</li><li>Vacancies</li></ul></div>
<div class="abs col" style="left:697px"><h3>Contact Details</h3><ul><li>42 Harbor Lane Suite 7 Austin 78701 TX</li><li class="big">512.555.0193</li><li>info@kalveron-mail.com</li><li>View our Location</li></ul></div>
<div class="abs footer-rule"></div>
<div class="abs copyright">© 2015 Company Name&nbsp; All right reserved&nbsp; Term of Use</div>

</body>
</html>
```